Personal Web page for recruiter and owner of consulting firm

I work full time as a recruiter so I want a page that allows for me to support my efforts. I would like a long single page, I need to be able to upload four two minute videos, and 4 images. I also want the color scheme to match with my consulting company. I own the domain marcusfenwold.net already through wordpress . I took a shot at it myself and its terrible.

Target Market(s)

Potential clients

Industry/Entity Type

Management Consulting

Logo Text

marcus fenwold

Font styles to use
Serif

Requirements
Must have
• Must in color scheme go well with my consulting company logo attached
• Must be able to upload 4 two minute videos and 4 images (photos of me)
• Single long scroll page
• Modern and clean
Nice to have
• Easy for me to update videos images and text without complex coding
Should not have
• I want the design and feel to go well with my logos not exactly replicate it

```html
<!DOCTYPE html>
<html lang="en">
<head>
<meta charset="utf-8">
<title>Fenwold Strategies – Recruiting &amp; Consulting Firm</title>
<link href="https://fonts.googleapis.com/css2?family=Montserrat:wght@400;500;600;700&family=Nunito+Sans:ital,wght@0,400;0,600;1,400&display=swap" rel="stylesheet">
<style>
:root{
  --navy:#062f5c;
  --navy-deep:#0a2a52;
  --sky:#7ab6e4;
  --sky-text:#6fb0e6;
  --grey-band:#ebebeb;
  --paper:#f4f5f7;
  --ink:#222;
  --muted:#777;
  --white:#fff;
}
*{margin:0;padding:0;box-sizing:border-box}
html,body{width:1200px;height:2965px;overflow:hidden}
body{font-family:"Nunito Sans",Arial,sans-serif;color:var(--ink);background:var(--white);position:relative}
.abs{position:absolute}

/* Hero */
.hero{position:absolute;left:0;top:0;width:1200px;height:640px;overflow:hidden}
.hero-photo{position:absolute;inset:0;background:linear-gradient(180deg,#8c7f78 0%,#a8968a 35%,#c2a887 70%,#b18f6c 100%)}
.hero-shade{position:absolute;inset:0;background:rgba(20,20,30,.18)}
.brand{position:absolute;left:135px;top:36px;color:var(--white);font-family:"Montserrat",sans-serif;font-weight:400;line-height:1}
.brand .name{font-size:34px;letter-spacing:3px;display:block}
.brand .sub{font-size:15px;letter-spacing:5px;display:block;margin-top:6px;padding-left:110px}
.nav{position:absolute;top:54px;right:148px;display:flex;gap:30px;font-family:"Montserrat",sans-serif;font-size:14px;color:var(--white)}
.hero h1{position:absolute;left:0;width:1200px;top:274px;text-align:center;color:var(--white);font-family:"Montserrat",sans-serif;font-weight:600;font-size:43px;letter-spacing:.5px}
.hero .tagline{position:absolute;left:0;width:1200px;top:338px;text-align:center;color:var(--sky-text);font-family:"Montserrat",sans-serif;font-weight:600;font-size:23px;letter-spacing:1px}
.dots{position:absolute;top:598px;left:534px;display:flex;gap:8px}
.dots span{width:26px;height:5px;background:var(--white)}
.dots span.on{background:var(--sky-text)}

/* About */
.about{position:absolute;top:640px;left:0;width:1200px;height:452px;background:var(--white)}
.about h2{position:absolute;left:142px;top:88px;font-family:"Montserrat",sans-serif;font-weight:400;font-size:29px;color:var(--ink)}
.about p{position:absolute;left:143px;width:360px;font-size:13px;line-height:27px;color:var(--muted)}
.btn-outline{position:absolute;display:flex;align-items:center;justify-content:center;font-family:"Montserrat",sans-serif;font-weight:600;font-size:11px;letter-spacing:.3px}
.about .btn-outline{left:145px;top:304px;width:137px;height:38px;border:2px solid var(--navy);color:var(--navy)}
.office-art{position:absolute;left:560px;top:50px;width:540px;height:402px;background:linear-gradient(180deg,#f6f3ee 0%,#e8dccb 60%,#b8875a 100%);border-radius:4px}

/* Services */
.services{position:absolute;top:1090px;left:0;width:1200px;height:495px}
.services svg.band{position:absolute;inset:0}
.services h2{position:absolute;top:40px;width:1200px;text-align:center;color:var(--white);font-family:"Montserrat",sans-serif;font-weight:400;font-size:26px}
.service{position:absolute;top:130px;width:320px;text-align:center;color:var(--white)}
.service svg{display:block;margin:0 auto;height:80px}
.service h3{font-family:"Montserrat",sans-serif;font-weight:400;font-size:20px;margin-top:28px}
.service p{font-size:12px;line-height:20px;color:#c7d3e3;margin:8px auto 0;width:300px}
.service .btn-outline{position:relative;margin:20px auto 0;width:120px;height:34px;border:1.5px solid var(--white);color:var(--white);font-size:10px}

/* Video */
.video{position:absolute;top:1507px;left:0;width:1200px;height:521px;background:var(--grey-band)}
.video h2{position:absolute;top:122px;width:1200px;text-align:center;font-family:"Montserrat",sans-serif;font-weight:400;font-size:28px;color:var(--ink)}
.clip{position:absolute;top:181px;width:420px;height:256px;border:4px solid var(--white);box-shadow:0 1px 3px rgba(0,0,0,.25)}
.clip .still{position:absolute;inset:0}
.clip .play{position:absolute;left:50%;top:50%;width:64px;height:64px;margin:-32px 0 0 -32px}

/* Testimonials */
.testimonials{position:absolute;top:2028px;left:0;width:1200px;height:385px;background:var(--sky)}
.testimonials h2{position:absolute;top:44px;width:1200px;text-align:center;color:var(--white);font-family:"Montserrat",sans-serif;font-weight:400;font-size:26px}
.avatar{position:absolute;width:102px;height:102px;border-radius:50%;border:4px solid var(--white);background:radial-gradient(circle at 50% 45%,#d9b9a2 0%,#a8806a 70%)}
.quote{position:absolute;width:288px;border:2px solid var(--white);border-radius:4px;padding:16px 22px;color:var(--white);font-style:italic;font-size:12.5px;line-height:21px}
.quote::before{content:"";position:absolute;left:-12px;top:42px;width:20px;height:20px;background:var(--sky);border-left:2px solid var(--white);border-bottom:2px solid var(--white);transform:rotate(45deg)}
.author{position:absolute;color:var(--white);font-size:13px;line-height:17px}
.author small{display:block;font-size:11px}

/* Contact */
.contact{position:absolute;top:2413px;left:0;width:1200px;height:492px;background:linear-gradient(180deg,#f7f8fa,#eef0f3)}
.contact h2{position:absolute;top:52px;width:1200px;text-align:center;font-family:"Montserrat",sans-serif;font-weight:400;font-size:27px;color:var(--ink)}
.info{position:absolute;left:200px;display:flex;gap:14px;font-size:15px;line-height:27px;color:#555}
.info svg{flex:none;width:24px;height:24px;margin-top:2px}
.contact .brand-dark{position:absolute;left:202px;top:316px;color:var(--navy-deep);font-family:"Montserrat",sans-serif;font-weight:400;line-height:1}
.brand-dark .name{display:block;font-size:32px;letter-spacing:3px}
.brand-dark .sub{display:block;font-size:15px;letter-spacing:4px;padding-left:80px;margin-top:6px}
.social{position:absolute;left:202px;top:400px;display:flex;gap:8px}
.social span{width:28px;height:28px;background:#4d6489}
.field{position:absolute;left:650px;width:400px;height:37px;background:var(--white);border:1px solid #d8dbe0;font-size:11px;color:#888;padding:10px 14px}
.submit{position:absolute;left:650px;top:390px;width:120px;height:40px;background:var(--sky);color:var(--white);font-family:"Montserrat",sans-serif;font-size:14px;display:flex;align-items:center;justify-content:center}

footer{position:absolute;top:2905px;left:0;width:1200px;height:60px;background:var(--navy);color:#c9d3e2;font-size:13px;display:flex;align-items:center;justify-content:center}
</style>
</head>
<body>

<header class="hero">
  <div class="hero-photo" role="img" aria-label="Photo of a team meeting around a table with laptops"></div>
  <div class="hero-shade"></div>
  <div class="brand"><span class="name">FENWOLD</span><span class="sub">STRATEGIES</span></div>
  <nav class="nav"><span>About Us</span><span>Our Services</span><span>Videos</span><span>Testimonials</span><span>Contact</span></nav>
  <h1>RECRUITING &amp; CONSULTING FIRM</h1>
  <div class="tagline">SUSPENDISSE RISUS NIBH ULTRICIES VOLUTPAT</div>
  <div class="dots"><span></span><span></span><span class="on"></span><span></span></div>
</header>

<section class="about">
  <h2>ABOUT COMPANY</h2>
  <p style="top:146px">consectetuer augue nisi quis lacus Ut ac mi quis lacus mollis aliquam Curabitur iaculis tempus eros</p>
  <p style="top:213px">ultrices Ut nisi erat fermentum vel congue id euismod in elit Fusce ultricies orci ac feugiat suscipit leo massa sodales velit et scelerisque mi tortor at ipsum Proin</p>
  <div class="btn-outline">READ MORE</div>
  <div class="office-art" role="img" aria-label="Illustration of an office desk with lamp, chair, bookshelf and wall clock"></div>
</section>

<section class="services">
  <svg class="band" width="1200" height="495" viewBox="0 0 1200 495"><polygon points="0,0 1200,0 1200,417 600,495 0,417" fill="#062f5c"/></svg>
  <h2>OUR SERVICES</h2>
  <div class="service" style="left:140px">
    <svg viewBox="0 0 80 80" fill="none" stroke="#fff" stroke-width="3"><circle cx="38" cy="42" r="32"/><circle cx="38" cy="42" r="21"/><circle cx="38" cy="42" r="10"/><path d="M38 42 L72 8 M62 8 h10 v10"/></svg>
    <h3>Business Consulting</h3>
    <p>Pellentesque nibh libero ultricies eu sagittis non mollis sed justo Praesent metus ipsum pulvinar pulvinar porta fringilla</p>
    <div class="btn-outline">READ MORE</div>
  </div>
  <div class="service" style="left:440px;top:124px">
    <svg viewBox="0 0 110 80" fill="none" stroke="#fff" stroke-width="3" stroke-linejoin="round"><path d="M4 24 h18 v32 h-18z M106 24 h-18 v32 h18z"/><path d="M22 28 l20-8 h14 l-14 14 q6 6 14 0 l12-8 l20 18 M22 52 l14 12 q4 4 8 0 l4 4 q4 4 8 0 l4 4 q4 4 8 0 l4 2 q4 2 8-2 l8-10"/></svg>
    <h3>Recruitment</h3>
    <p>Pellentesque nibh libero ultricies eu sagittis non mollis sed justo Praesent metus ipsum pulvinar pulvinar porta fringilla</p>
    <div class="btn-outline">READ MORE</div>
  </div>
  <div class="service" style="left:770px;top:128px">
    <svg viewBox="0 0 80 80" fill="#fff"><circle cx="34" cy="26" r="14"/><path d="M8 78 q0-30 26-34 q26 4 26 34z"/><path d="M30 44 l4 8 l4-8z" fill="#062f5c"/><rect x="46" y="2" width="30" height="20" rx="2" fill="none" stroke="#fff" stroke-width="2.5"/><path d="M52 22 l-4 8 l10-8z"/></svg>
    <h3>Job Consulting</h3>
    <p>Pellentesque nibh libero ultricies eu sagittis non mollis sed justo Praesent metus ipsum pulvinar pulvinar porta fringilla</p>
    <div class="btn-outline">READ MORE</div>
  </div>
</section>

<section class="video">
  <h2>OUR VIDEO</h2>
  <div class="clip" style="left:158px">
    <div class="still" role="img" aria-label="Video still of hands using a phone and laptop" style="background:linear-gradient(135deg,#4a5560 0%,#2f3a45 50%,#6b5a40 100%)"></div>
    <svg class="play" viewBox="0 0 64 64"><circle cx="32" cy="32" r="32" fill="#fff"/><polygon points="25,19 25,45 46,32" fill="#111"/></svg>
  </div>
  <div class="clip" style="left:624px">
    <div class="still" role="img" aria-label="Video still of a hand pointing at a tablet showing a recruitment page" style="background:linear-gradient(135deg,#c9ccd0 0%,#8fa3b0 50%,#d8d6d0 100%)"></div>
    <svg class="play" viewBox="0 0 64 64"><circle cx="32" cy="32" r="32" fill="#fff"/><polygon points="25,19 25,45 46,32" fill="#111"/></svg>
  </div>
</section>

<section class="testimonials">
  <h2>TESTIMONIALS</h2>
  <div class="avatar" style="left:154px;top:114px" role="img" aria-label="Portrait of client"></div>
  <div class="quote" style="left:265px;top:108px">Suspendisse risus nibh ultricies eu volutpat non condimentum hendrerit augue Etiam eleifend metus vitae adipiscing semper mauris ipsum iaculis elit con</div>
  <div class="author" style="left:270px;top:282px">By Author Name<small>City, Location</small></div>
  <div class="avatar" style="left:600px;top:110px" role="img" aria-label="Portrait of client"></div>
  <div class="quote" style="left:712px;top:102px">Etiam nulla massa pharetra facilisis volut pat in imperdiet sit amet sem Aliquam nec erat at purus cursus interd um Vestibulum ligula augue bibendum accumsan vest</div>
  <div class="author" style="left:716px;top:276px">By Author Name<small>City, Location</small></div>
</section>

<section class="contact">
  <h2>CONTACT US</h2>
  <div class="info" style="top:136px">
    <svg viewBox="0 0 24 24"><rect width="24" height="24" fill="#4d6489"/><path d="M12 4a5 5 0 0 0-5 5c0 4 5 10 5 10s5-6 5-10a5 5 0 0 0-5-5zm0 7a2 2 0 1 1 0-4 2 2 0 0 1 0 4z" fill="#fff"/></svg>
    <div>412 Harbor View Road Suite B20<br>Millbrook, PA 19110</div>
  </div>
  <div class="info" style="top:224px">
    <svg viewBox="0 0 24 24"><rect width="24" height="24" fill="#4d6489"/><path d="M7 5h3l1.5 4-2 1.3a9 9 0 0 0 4.2 4.2l1.3-2 4 1.5v3a1.5 1.5 0 0 1-1.6 1.5A13 13 0 0 1 5.5 6.6 1.5 1.5 0 0 1 7 5z" fill="#fff"/></svg>
    <div>(555) 214-3080</div>
  </div>
  <div class="info" style="top:256px">
    <svg viewBox="0 0 24 24"><rect width="24" height="24" fill="#4d6489"/><rect x="5" y="7" width="14" height="10" fill="#fff"/><path d="M5 7l7 6 7-6" fill="none" stroke="#4d6489" stroke-width="1.5"/></svg>
    <div>info@marcusfenwold.net</div>
  </div>
  <div class="brand-dark"><span class="name">FENWOLD</span><span class="sub">STRATEGIES</span></div>
  <div class="social"><span></span><span></span><span></span><span></span><span></span></div>

  <div class="field" style="top:142px">Name</div>
  <div class="field" style="top:190px">Email address</div>
  <div class="field" style="top:239px">Phone</div>
  <div class="field" style="top:287px;height:93px">Message</div>
  <div class="submit">SUBMIT</div>
</section>

<footer>© 2017 Company Name &nbsp;All right reserved &nbsp;Term of Use</footer>

</body>
</html>
```